Icons/images for company values

We have five company values, we have a new logo and a new look. I would like drawn images for each value that are in keeping with our look and feel.

Target Market(s)

internal/staff

Industry/Entity Type

media compliance

Requirements
Must have
• colours aligned with logo.

```html
<!DOCTYPE html>
<html lang="en">
<head>
<meta charset="utf-8">
<title>Company Values</title>
<link rel="stylesheet" href="https://fonts.googleapis.com/css2?family=Montserrat:wght@400;500;800&display=swap">
<style>
  :root {
    --page: #e8e8e8;
    --teal: #31afbe;
    --aqua: #52c6cc;
    --mint: #5ed9a6;
    --lime: #c2e56e;
    --blue: #1a86c7;
    --ink: #1c2a2f;
    --soft: #f4f5f7;
    --white: #ffffff;
  }
  * { margin: 0; padding: 0; box-sizing: border-box; }
  html, body { width: 1200px; height: 777px; overflow: hidden; background: var(--page); }
  body { font-family: "Montserrat", Arial, sans-serif; color: var(--ink); }
  .values-board {
    position: absolute; left: 0; top: 51px; width: 1200px; height: 674px;
    background: var(--soft); overflow: hidden;
  }
  .values-wheel { position: absolute; left: 0; top: 0; }
  .brand-name {
    position: absolute; left: 30px; top: 306px; width: 240px;
    font-size: 56px; font-weight: 400; letter-spacing: 14px;
    color: var(--blue); line-height: 64px;
  }
  .value-list { position: absolute; left: 617px; top: 0; width: 583px; height: 674px; }
  .value-row { position: absolute; left: 0; width: 583px; padding: 0 90px 0 39px; }
  .value-row h2 {
    font-size: 19.5px; font-weight: 800; line-height: 21px; text-transform: uppercase;
    color: var(--ink); margin-bottom: 10px;
  }
  .value-row p { font-size: 13px; font-weight: 500; line-height: 16.5px; color: var(--ink); }
  .row-1 { top: 0; height: 134px; background: var(--teal); padding-top: 32px; }
  .row-2 { top: 134px; height: 134px; background: var(--aqua); padding-top: 32px; }
  .row-2 h2 { margin-bottom: 26px; }
  .row-3 { top: 268px; height: 137px; background: var(--mint); padding-top: 20px; }
  .row-3 h2 { margin-bottom: 18px; }
  .row-4 { top: 405px; height: 135px; background: var(--lime); padding-top: 24px; }
  .row-4 h2 { margin-bottom: 16px; }
  .row-5 { top: 540px; height: 134px; background: var(--teal); padding-top: 22px; }
  .row-5 h2 { margin-bottom: 12px; }
  .value-number {
    position: absolute; left: 592px; width: 50px; height: 50px; border-radius: 50%;
    background: var(--white); border: 3px solid var(--mint);
    box-shadow: 0 2px 5px rgba(0,0,0,.25);
    font-size: 19px; font-weight: 800; color: var(--ink);
    display: flex; align-items: center; justify-content: center;
  }
</style>
</head>
<body>
<main class="values-board">
  <svg class="values-wheel" width="617" height="674" viewBox="0 0 617 674">
    <defs>
      <linearGradient id="ringGrad" x1="0" y1="0" x2="0" y2="1">
        <stop offset="0" stop-color="#1a86c7"/>
        <stop offset="0.5" stop-color="#52c6cc"/>
        <stop offset="1" stop-color="#c2e56e"/>
      </linearGradient>
    </defs>
    <circle cx="107" cy="338" r="366" fill="none" stroke="url(#ringGrad)" stroke-width="7"/>
    <circle cx="107" cy="338" r="358" fill="var(--teal)"/>
    <path class="sector-together" d="M107 338 L307.6 42.8 A357 357 0 0 1 431.5 189.5 Z" fill="var(--aqua)" stroke="#fff" stroke-width="3"/>
    <path class="sector-leaders" d="M107 338 L431.5 189.5 A357 357 0 0 1 454.7 419.4 Z" fill="var(--mint)" stroke="#fff" stroke-width="3"/>
    <path class="sector-done" d="M107 338 L454.7 419.4 A357 357 0 0 1 337.3 610.7 Z" fill="var(--lime)" stroke="#fff" stroke-width="3"/>
    <circle cx="107" cy="338" r="203" fill="#fff"/>
    <g class="connectors" stroke-width="2.5" fill="#fff">
      <line x1="301" y1="29" x2="600" y2="29" stroke="#1a86c7"/>
      <line x1="443" y1="189" x2="600" y2="189" stroke="#31afbe"/>
      <line x1="474" y1="331" x2="600" y2="331" stroke="#5ed9a6"/>
      <line x1="447" y1="482" x2="600" y2="482" stroke="#8fdc8a"/>
      <line x1="338" y1="625" x2="600" y2="625" stroke="#c2e56e"/>
      <circle cx="301" cy="29" r="5.5" stroke="#1a86c7"/>
      <circle cx="443" cy="189" r="5.5" stroke="#31afbe"/>
      <circle cx="474" cy="331" r="5.5" stroke="#5ed9a6"/>
      <circle cx="447" cy="482" r="5.5" stroke="#8fdc8a"/>
      <circle cx="338" cy="625" r="5.5" stroke="#c2e56e"/>
    </g>
    <g class="value-icons" fill="var(--blue)">
      <circle cx="116" cy="76" r="34" role="img" aria-label="Icon of a hand holding a heart"/>
      <circle cx="323" cy="183" r="36" role="img" aria-label="Icon of three people standing together"/>
      <circle cx="386" cy="338" r="36" role="img" aria-label="Icon of a person with a star badge"/>
      <circle cx="352" cy="479" r="36" role="img" aria-label="Icon of a target with an arrow"/>
      <circle cx="131" cy="596" r="38" role="img" aria-label="Icon of a connected team of people"/>
    </g>
  </svg>

  <div class="brand-name">ARVO</div>

  <section class="value-list">
    <article class="value-row row-1">
      <h2>We're open and honest</h2>
      <p>Sharing information helps us achieve the best outcomes for our teams and business. We value open, honest, and clear communication.</p>
    </article>
    <article class="value-row row-2">
      <h2>We get there faster, together</h2>
      <p>Collaboration is at the heart of what we do, no matter our team.</p>
    </article>
    <article class="value-row row-3">
      <h2>We are leaders in copyright and intellectual property</h2>
      <p>Leading the conversation in audio-visual copyright compliance and advocating for the protection of intellectual property globally.</p>
    </article>
    <article class="value-row row-4">
      <h2>We get things done</h2>
      <p>We grow through capability, focus and hard work. We believe small steps compound to big results.</p>
    </article>
    <article class="value-row row-5">
      <h2>Diverse perspectives build better outcomes</h2>
      <p>We value diversity, inclusion, respect and trust within our teams. We are building a truly global organisation.</p>
    </article>
  </section>

  <div class="value-number" style="top:4px">01</div>
  <div class="value-number" style="top:164px">02</div>
  <div class="value-number" style="top:306px">03</div>
  <div class="value-number" style="top:457px">04</div>
  <div class="value-number" style="top:600px">05</div>
</main>
</body>
</html>
```